Jewelers Website

This is for the DESIGN ONLY.
I am a software programmer and will be doing the development.
New website design for
www.lunacrestgems.com.au
Need a fresh new look for an online only jewellery business who produce their jewellery by hand. I would like it designed in a parallax style. Feel free to recommend fonts to use for the site. This is an Australian based company located in NSW so shots of sites in NSW might make nice background images.
http://vornaplex.me/demo/#theme=parallax
To contain the below sections
About Us
Contact Us
Gallery
Testimonials
Diamond Types
The colour scheme is to be Black / White and Silver.
With the Parallax style there will be moving sections and images for added impact.
Target Market(s)
Young Adults mainly engagement jewellery

```html
<!DOCTYPE html>
<html lang="en">
<head>
<meta charset="utf-8">
<title>Lunacrest Gems</title>
<link rel="stylesheet" href="https://fonts.googleapis.com/css2?family=Cinzel:wght@400;700&family=Lato:wght@400;700;900&display=swap">
<style>
  :root {
    --black: #000000;
    --ink: #111111;
    --white: #ffffff;
    --silver: #cfcfcf;
    --grey-text: #444444;
    --field: #d9d9d9;
    --rule: rgba(255,255,255,0.25);
    --heading: "Cinzel", Georgia, serif;
    --body: "Lato", Arial, sans-serif;
  }
  * { box-sizing: border-box; margin: 0; padding: 0; }
  html, body { width: 1200px; height: 3750px; overflow: hidden; }
  body { position: relative; background: var(--white); font-family: var(--body); color: var(--ink); }
  .abs { position: absolute; }

  /* Hero */
  .hero { position: absolute; left: 0; top: 0; width: 1200px; height: 950px; background: var(--black); overflow: hidden; }
  .hero-photo { position: absolute; inset: 0;
    background: radial-gradient(ellipse 520px 620px at 820px 420px, #7a6a63 0%, #4a3a36 35%, #1e1413 65%, #0a0606 100%); }
  .topbar { position: absolute; top: 14px; left: 142px; right: 142px; display: flex; justify-content: space-between;
    color: var(--white); font-size: 12px; letter-spacing: 0.5px; }
  .topbar .auth span { margin-left: 26px; }
  .logo { position: absolute; top: 62px; left: 0; width: 1200px; text-align: center; color: var(--white);
    font-family: var(--heading); font-size: 38px; line-height: 36px; letter-spacing: 1px; }
  .nav { position: absolute; top: 192px; left: 0; width: 1200px; height: 48px; border-top: 1px solid var(--rule);
    border-bottom: 1px solid var(--rule); display: flex; justify-content: center; gap: 82px; align-items: center;
    color: var(--white); font-family: var(--heading); font-size: 13px; letter-spacing: 1px; }
  .hero-copy { position: absolute; left: 142px; top: 466px; color: var(--white); }
  .hero-title { font-family: var(--heading); font-size: 29px; line-height: 42px; letter-spacing: 2px; }
  .hero-sub { margin-top: 18px; font-family: var(--heading); font-size: 17px; letter-spacing: 2px; color: var(--silver); }
  .hero-cta { margin-top: 26px; font-size: 13px; font-weight: 700; letter-spacing: 1px; display: flex; align-items: center; gap: 14px; }

  /* Section headings */
  .section-title { font-family: var(--heading); font-size: 40px; letter-spacing: 2px; text-align: center; }
  .section-sub { font-size: 17px; letter-spacing: 1px; text-align: center; }

  /* About */
  .about-title { left: 142px; top: 1030px; font-family: var(--heading); font-size: 40px; letter-spacing: 2px; }
  .about-text { left: 142px; top: 1125px; width: 580px; font-size: 14px; line-height: 29px; color: var(--grey-text); }
  .about-photo { left: 750px; top: 1015px; width: 250px; height: 390px;
    background: linear-gradient(180deg, #ffffff 0%, #d8d8d8 20%, #9a9a9a 45%, #e6e6e6 62%, #ffffff 100%); border-radius: 8px; }

  /* Gallery */
  .gallery { left: 0; top: 1450px; width: 1200px; height: 562px; background: var(--black); color: var(--white); }
  .gallery .section-title { margin-top: 52px; }
  .gallery .section-sub { margin-top: 16px; }
  .gallery-text { width: 930px; margin: 10px auto 0; font-size: 14px; line-height: 24px; text-align: center; }
  .tiles { position: absolute; left: 110px; top: 232px; width: 980px; height: 238px; display: flex; }
  .tile { width: 245px; height: 238px; position: relative; }
  .tile-1 { background: linear-gradient(135deg, #3a2a4a, #c59a4a 60%, #7a5a2a); }
  .tile-2 { background: linear-gradient(180deg, #222 0%, #555 50%, #1a1a1a 100%); }
  .tile-3 { background: linear-gradient(135deg, #c26a2a, #f0b060 50%, #8a4a1a); }
  .tile-4 { background: linear-gradient(135deg, #1a1a1a, #8a8a8a 55%, #2a2a2a); }
  .tile-caption { position: absolute; left: 30px; right: 0; bottom: 0; height: 92px; background: var(--black);
    text-align: center; padding-top: 24px; }
  .tile-caption .cap-title { font-size: 14px; letter-spacing: 0.5px; }
  .tile-caption .cap-sub { font-size: 11px; margin-top: 12px; }
  .tile-icons { position: absolute; left: 60px; top: 60px; display: flex; gap: 16px; }
  .tile-icons span { width: 42px; height: 42px; border-radius: 50%; background: rgba(80,80,80,0.85); display: flex; align-items: center; justify-content: center; }
  .arrow { position: absolute; top: 337px; }

  /* Testimonials */
  .testimonials { left: 0; top: 2012px; width: 1200px; height: 470px; }
  .testimonials .section-title { margin-top: 50px; }
  .testimonials .section-sub { margin-top: 14px; }
  .avatar { position: absolute; left: 538px; top: 160px; width: 124px; height: 124px; border-radius: 50%;
    background: radial-gradient(circle at 50% 45%, #f2c9a2, #c77a3a 70%, #8a4a2a); }
  .quote { position: absolute; top: 308px; left: 140px; width: 920px; font-size: 14px; line-height: 24px; text-align: center; color: var(--grey-text); }
  .client { position: absolute; top: 372px; width: 1200px; text-align: center; font-size: 16px; letter-spacing: 1px; }
  .dots { position: absolute; top: 408px; width: 1200px; display: flex; justify-content: center; gap: 10px; }
  .dots span { width: 9px; height: 9px; border-radius: 50%; background: #999; }
  .dots span:first-child { background: #333; }

  /* Diamond types */
  .types { left: 0; top: 2482px; width: 1200px; height: 493px;
    background: linear-gradient(90deg, #6a6a6a 0%, #3a3a3a 35%, #111 55%, #000 100%); color: var(--white); }
  .types-title { position: absolute; left: 592px; top: 80px; font-family: var(--heading); font-size: 40px; letter-spacing: 2px; }
  .types-text { position: absolute; left: 592px; top: 152px; width: 565px; font-size: 14px; line-height: 30px; }

  /* Contact */
  .contact-title { top: 3015px; left: 0; width: 1200px; }
  .contact-sub { top: 3088px; left: 0; width: 1200px; }
  .map { left: 137px; top: 3178px; width: 453px; height: 222px; background: linear-gradient(135deg, #e8e6df, #d7dccf 50%, #ece8d8); border: 1px solid #ccc; }
  .info-title { left: 137px; top: 3450px; font-size: 26px; font-weight: 900; }
  .info-list { left: 137px; top: 3494px; font-size: 13px; line-height: 30px; }
  .info-list b { font-weight: 700; }
  .enquiry { left: 607px; top: 3175px; width: 455px; height: 450px; background: var(--black); color: var(--white); padding: 14px 22px; }
  .enquiry h3 { font-size: 26px; font-weight: 900; }
  .field-label { font-size: 13px; margin-top: 10px; }
  .field-label em { font-style: normal; color: #888; font-size: 11px; }
  .field { margin-top: 6px; width: 412px; height: 38px; background: var(--field); }
  .field.tall { height: 162px; }
  .send { position: absolute; right: 22px; bottom: 14px; width: 122px; height: 38px; background: var(--white); color: var(--black);
    font-size: 13px; display: flex; align-items: center; justify-content: center; }

  /* Footer */
  .footer { left: 0; top: 3688px; width: 1200px; height: 62px; background: var(--black); color: var(--white);
    font-size: 12px; display: flex; align-items: center; justify-content: center; }
  .to-top { position: absolute; left: 1042px; top: 6px; }
</style>
</head>
<body>

<header class="hero">
  <div class="hero-photo" role="img" aria-label="Model wearing a silver necklace with black drop stones and matching earring"></div>
  <div class="topbar"><span>INFO@LUNACRESTGEMS.COM</span><span class="auth"><span>LOGIN</span><span>|</span><span>SIGNUP</span></span></div>
  <div class="logo">LUNACREST<br>GEMS</div>
  <nav class="nav"><span>HOME</span><span>ABOUT US</span><span>GALLERY</span><span>TESTIMONIALS</span><span>DIAMOND TYPES</span><span>CONTACT US</span></nav>
  <div class="hero-copy">
    <div class="hero-title">THE BLACK NECKLACE<br>WITH SILVER STYLE</div>
    <div class="hero-sub">HIGH JEWELLERY COLLECTION</div>
    <div class="hero-cta"><svg width="10" height="12"><path d="M0 0 L10 6 L0 12 Z" fill="#fff"/></svg>DISCOVER THE COLLECTION</div>
  </div>
  <svg class="abs" style="left:105px;top:867px" width="50" height="50"><circle cx="25" cy="25" r="23" fill="none" stroke="#fff" stroke-width="1.5"/><path d="M15 21 L25 31 L35 21" fill="none" stroke="#fff" stroke-width="1.5"/></svg>
</header>

<h2 class="abs about-title">About Lunacrest Gems</h2>
<div class="abs about-text">
  <p>At Lunacrest Gems we are passionate about fine jewellery and gems. We feature one of a kind, original and elegant, handmade pieces. Lunacrest Gems handmade jewellery is crafted using exceptional quality metals, integrating designs that are innovative, creative, and unique.</p>
  <p>After you have consulted with our experienced staff - our highly trained and experienced jewellers hand-make every piece of finely crafted jewellery with a level of care and attention that cannot be matched by machines. Our custom jewellery is Australian-made in our Sydney workshop.</p>
</div>
<div class="abs about-photo" role="img" aria-label="Silver diamond ring with a rectangular centre stone and its reflection"></div>

<section class="abs gallery">
  <h2 class="section-title">Gallery</h2>
  <p class="section-sub">BEST &amp; MOST POPULAR OF OUR WORKS</p>
  <p class="gallery-text">Lorem ipsum dolor sit amet, consectetuer adipiscing elit, sed diam nonummy nibh euismod tincidunt ut laoreet dolore magna aliquam erat volutpat. Ut wisi enim ad minim veniam, quis nostrud exerci tation ullamcorper suscipit lobortis nisl ut aliquip ex ea commodo consequat.</p>
  <div class="tiles">
    <div class="tile tile-1" role="img" aria-label="Gold ring with a pearl and diamond petals"></div>
    <div class="tile tile-2" role="img" aria-label="Woman in black wearing a necklace">
      <div class="tile-icons">
        <span><svg width="16" height="18"><path d="M2 1 H10 L14 5 V17 H2 Z" fill="#fff"/></svg></span>
        <span><svg width="18" height="18"><path d="M7 11 L11 7 M5 9 L3 11 A3 3 0 0 0 7 15 L9 13 M9 5 L11 3 A3 3 0 0 1 15 7 L13 9" stroke="#fff" stroke-width="2" fill="none"/></svg></span>
        <span><svg width="18" height="18"><circle cx="8" cy="8" r="5" stroke="#fff" stroke-width="2" fill="none"/><path d="M12 12 L16 16 M6 8 H10 M8 6 V10" stroke="#fff" stroke-width="2"/></svg></span>
      </div>
      <div class="tile-caption"><div class="cap-title">LOREM IPSUM DOLOR SIT</div><div class="cap-sub">Amet adicsing consectutuer</div></div>
    </div>
    <div class="tile tile-3" role="img" aria-label="Gold flower pendant set with diamonds"></div>
    <div class="tile tile-4" role="img" aria-label="Black and white hands with a diamond ring"></div>
  </div>
  <svg class="arrow" style="left:120px" width="16" height="28"><path d="M14 2 L3 14 L14 26" fill="none" stroke="#fff" stroke-width="3"/></svg>
  <svg class="arrow" style="left:1064px" width="16" height="28"><path d="M2 2 L13 14 L2 26" fill="none" stroke="#fff" stroke-width="3"/></svg>
</section>

<section class="abs testimonials">
  <h2 class="section-title">Clients &amp; Testimonials</h2>
  <p class="section-sub">MORE THAN 2000 OF HAPPY CUSTOMERS</p>
  <div class="avatar" role="img" aria-label="Client portrait illustration"></div>
  <p class="quote">Lorem ipsum dolor sit amet, consectetuer adipiscing elit, sed diam nonummy nibh euismod tincidunt ut laoreet dolore magna aliquam erat volutpat. Ut wisi enim ad minim veniam, quis nostrud exerci tation ullamcorper suscipit lobortis nisl ut aliquip ex ea commodo consequat.</p>
  <div class="client">MARA VELLONI</div>
  <div class="dots"><span></span><span></span><span></span><span></span></div>
</section>

<section class="abs types" role="img" aria-label="Loose cut diamonds on a dark surface">
  <h2 class="types-title">Types Of Diamonds</h2>
  <p class="types-text">Lorem ipsum dolor sit amet, consectetuer adipiscing elit, sed diam nonummy nibh euismod tincidunt ut laoreet dolore magna aliquam erat volutpat. Ut wisi enim ad minim veniam, quis nostrud exerci tation ullamcorper suscipit lobortis nisl ut aliquip ex ea commodo consequat. Duis autem vel eum iriure dolor in hendrerit in vulputate velit esse molestie consequat, vel illum dolore eu feugiat nulla facilisis at vero eros et accumsan et iusto odio dignissim qui blandit praesent luptatum zzril delenit augue duis dolore te feugait nulla facilisi.</p>
</section>

<h2 class="abs section-title contact-title">Contact Us</h2>
<p class="abs section-sub contact-sub">LOREM IPSUM DOLOR SIT AMET CONSECTUTUER</p>
<div class="abs map" role="img" aria-label="Street map showing the workshop location"></div>
<h3 class="abs info-title">CONTACT INFO</h3>
<div class="abs info-list">
  <div>Kellview NSW 2299, Australia</div>
  <div><b>Phone:</b> +1 200 555 0145</div>
  <div><b>Fax:</b> +1 100 555 0188</div>
  <div><b>Email:</b> hello@lunacrestmail.com</div>
  <div><b>Web:</b> http://www.lunacrestgems.com.au/</div>
</div>
<form class="abs enquiry">
  <h3>ENQUIRY</h3>
  <div class="field-label">Your Name <em>(required)</em></div><div class="field"></div>
  <div class="field-label">E-mail <em>(required)</em></div><div class="field"></div>
  <div class="field-label">Message <em>(required)</em></div><div class="field tall"></div>
  <div class="send">SEND EMAIL</div>
</form>

<footer class="abs footer">
  © Copyright 2002-2014 Lunacrest Gems Pty Ltd
  <svg class="to-top" width="50" height="50"><circle cx="25" cy="25" r="23" fill="none" stroke="#fff" stroke-width="1.5"/><path d="M15 29 L25 19 L35 29" fill="none" stroke="#fff" stroke-width="1.5"/></svg>
</footer>

</body>
</html>
```